Local fast-growing company in the service sector

We are looking for a modern business card design, which should also appear on our letterheads

Target Market(s)

Private and industrial sectors

Contact Information for Business Card

Vorname Name
Kellberger Str. 18
73614 Schorndorf
Tel.: 07146-839214-0
Name@agentur-kvtl.de

Colors
9d9d9d
919191
aaaaaa

Requirements
Must have
• The logo (file) in silver

```html
<!DOCTYPE html>
<html lang="de">
<head>
<meta charset="utf-8">
<title>KVTL Visitenkarte</title>
<link href="https://fonts.googleapis.com/css2?family=PT+Sans:wght@400;700&display=swap" rel="stylesheet">
<style>
  :root {
    --stage: #2b2b2b;
    --card-black: #141414;
    --card-white: #ffffff;
    --silver: #aaaaaa;
    --silver-mid: #9d9d9d;
    --silver-dark: #919191;
    --text-light: #ffffff;
  }
  * { box-sizing: border-box; margin: 0; padding: 0; }
  html, body {
    width: 1200px; height: 900px; overflow: hidden;
    background: var(--stage);
    font-family: "PT Sans", Arial, sans-serif;
  }
  .stage {
    position: relative; width: 1200px; height: 900px;
    display: flex; flex-direction: column; align-items: center; justify-content: center; gap: 24px;
  }
  .card {
    position: relative; width: 700px; height: 400px; overflow: hidden;
    box-shadow: 0 10px 30px rgba(0,0,0,.45);
  }
  .brand {
    display: flex; align-items: center; gap: 18px;
    font-weight: 700; letter-spacing: 2px; line-height: 1;
  }
  .brand-square { display: block; flex: none; }

  .card-back {
    background: var(--card-black);
    display: flex; align-items: center; justify-content: center;
  }
  .card-back .brand { color: var(--silver); font-size: 92px; }
  .card-back .brand-square { width: 56px; height: 56px; background: var(--silver); }

  .card-front { background: var(--card-white); }
  .front-band {
    position: absolute; left: 0; right: 0; top: 225px; bottom: 0;
    background: linear-gradient(100deg, var(--silver-dark) 0%, var(--silver) 55%, var(--silver-mid) 100%);
  }
  .card-front .brand {
    position: absolute; left: 150px; top: 95px;
    color: var(--silver-mid); font-size: 96px;
  }
  .card-front .brand-square { width: 60px; height: 60px; background: var(--silver-mid); }

  .contact-list {
    position: absolute; right: 26px; top: 240px;
    list-style: none; color: var(--text-light);
    font-size: 19px; line-height: 1.35; text-align: right;
  }
  .contact-list li { display: flex; align-items: center; justify-content: flex-end; gap: 8px; }
  .contact-list svg { width: 16px; height: 16px; flex: none; }

  .person {
    position: absolute; left: 34px; bottom: 34px;
    color: var(--text-light); font-size: 19px; line-height: 1.3;
  }
  .person-name { font-weight: 700; text-transform: uppercase; letter-spacing: .5px; }
</style>
</head>
<body>
<main class="stage">
  <section class="card card-back" aria-label="Kartenrückseite">
    <div class="brand"><span class="brand-square"></span><span class="brand-name">KVTL</span></div>
  </section>

  <section class="card card-front" aria-label="Kartenvorderseite">
    <div class="front-band"></div>
    <div class="brand"><span class="brand-square"></span><span class="brand-name">KVTL</span></div>

    <ul class="contact-list">
      <li>07146-839214-0
        <svg viewBox="0 0 16 16" aria-hidden="true"><path fill="#fff" d="M4 1.5l2.2 3-1.3 1.6c.9 2 2.1 3.2 4 4l1.6-1.3 3 2.2-1.2 2.5C7.2 13.2 2.8 8.8 1.5 3.7z"/></svg>
      </li>
      <li>Name@agentur-kvtl.de
        <svg viewBox="0 0 16 16" aria-hidden="true"><rect x="1.5" y="3.5" width="13" height="9" fill="#fff"/><path d="M1.5 3.5l6.5 5 6.5-5" fill="none" stroke="#9d9d9d" stroke-width="1.2"/></svg>
      </li>
      <li>www.agentur-kvtl.de
        <svg viewBox="0 0 16 16" aria-hidden="true"><circle cx="8" cy="8" r="6.5" fill="none" stroke="#fff" stroke-width="1.4"/><path d="M1.5 8h13M8 1.5c-2.5 3-2.5 10 0 13M8 1.5c2.5 3 2.5 10 0 13" fill="none" stroke="#fff" stroke-width="1.1"/></svg>
      </li>
    </ul>

    <div class="person">
      <p class="person-name">Lena Hofmann</p>
      <p>Kellberger Str. 18</p>
      <p>73614 Schorndorf</p>
    </div>
  </section>
</main>
</body>
</html>
```